Private Dining Restaurant Menu Design

Looking for help in designing a private dining room menu brochure - probably would need 4 panel layout to make all of the content fit, or a 5.5x8" booklet. Open to your ideas on layout/vessel - would want to post on website and be able to print to hand out to guests interested in booking our private dining room.

All content is in the attached "Private Dining Menu".

Would like to match existing dinner menu design - also attached.

Website is www.copperkettlebistro.com

Requirements
Must have
• Easy to read format of a brochure of the private dining menu content - want to be able to hand out to interested guests and have it simple and easy to read/flip through.

```html
<!DOCTYPE html>
<html lang="en">
<head>
<meta charset="utf-8">
<title>Dinner Options</title>
<link rel="stylesheet" href="https://fonts.googleapis.com/css2?family=Righteous&family=Merriweather:ital,wght@0,400;0,700;1,400&display=swap">
<style>
  :root {
    --bg: #2b2b30;
    --ink: #ffffff;
    --gold-light: #f3dc8a;
    --gold: #d2a93f;
    --gold-deep: #a8792a;
    --bullet-dim: #4a4a50;
    --photo-top: #8a8275;
    --photo-bottom: #3e3833;
  }
  html, body {
    margin: 0;
    padding: 0;
    width: 849px;
    height: 1200px;
    overflow: hidden;
    background: var(--bg);
  }
  .page {
    position: relative;
    width: 1000px;
    height: 1413px;
    transform: scale(0.849);
    transform-origin: 0 0;
    background: var(--bg);
    font-family: "Merriweather", Georgia, serif;
    color: var(--ink);
  }
  .frame {
    position: absolute;
    inset: 0;
  }
  .title {
    position: absolute;
    top: 108px;
    left: 0;
    width: 1000px;
    margin: 0;
    text-align: center;
    font-family: "Righteous", "Arial Black", sans-serif;
    font-weight: 400;
    font-size: 56px;
    letter-spacing: 2px;
    line-height: 1;
    background: linear-gradient(180deg, var(--gold-light) 0%, var(--gold) 50%, var(--gold-deep) 100%);
    -webkit-background-clip: text;
    background-clip: text;
    color: transparent;
  }
  .subtitle {
    position: absolute;
    top: 168px;
    left: 0;
    width: 1000px;
    margin: 0;
    text-align: center;
    font-size: 16.5px;
  }
  .note {
    position: absolute;
    top: 254px;
    left: 80px;
    width: 840px;
    margin: 0;
    text-align: center;
    font-size: 16.5px;
    line-height: 26px;
  }
  .option {
    position: absolute;
    left: 72px;
    width: 760px;
  }
  .option-a { top: 334px; }
  .option-b { top: 574px; }
  .option-title {
    margin: 0 0 6px;
    font-size: 24px;
    font-weight: 700;
    line-height: 32px;
  }
  .option-desc {
    margin: 0 0 22px;
    font-style: italic;
    font-size: 16.5px;
    line-height: 24px;
    width: 640px;
  }
  .dishes {
    list-style: none;
    margin: 0;
    padding: 0;
    font-size: 16.5px;
    line-height: 26px;
  }
  .dishes li {
    position: relative;
    padding-left: 30px;
  }
  .dishes li::before {
    content: "•";
    position: absolute;
    left: 0;
    color: var(--ink);
  }
  .option-a .dishes li::before { color: var(--bullet-dim); }
  .gold-bar {
    position: absolute;
    height: 12px;
    background: linear-gradient(90deg, var(--gold-deep), var(--gold-light) 35%, var(--gold) 65%, var(--gold-deep));
  }
  .bar-top { top: 800px; left: 75px; width: 780px; }
  .bar-bottom { top: 1303px; left: 100px; width: 780px; }
  .room-photo {
    position: absolute;
    top: 840px;
    left: 163px;
    width: 604px;
    height: 428px;
    background: linear-gradient(180deg, var(--photo-top) 0%, #6b6358 45%, var(--photo-bottom) 100%);
  }
</style>
</head>
<body>
<div class="page">
  <svg class="frame" width="1000" height="1413" viewBox="0 0 1000 1413" aria-hidden="true">
    <defs>
      <linearGradient id="frameGold" x1="0" y1="0" x2="1" y2="1">
        <stop offset="0" stop-color="#f3dc8a"/>
        <stop offset="0.5" stop-color="#d2a93f"/>
        <stop offset="1" stop-color="#f0d27a"/>
      </linearGradient>
    </defs>
    <path d="M58 22 H944 A42 42 0 0 0 986 64 V1348 A42 42 0 0 0 944 1390 H58 A42 42 0 0 0 16 1348 V64 A42 42 0 0 0 58 22 Z"
          fill="none" stroke="url(#frameGold)" stroke-width="3"/>
    <path d="M70 40 H930 A34 34 0 0 0 964 74 V1338 A34 34 0 0 0 930 1372 H70 A34 34 0 0 0 36 1338 V74 A34 34 0 0 0 70 40 Z"
          fill="none" stroke="url(#frameGold)" stroke-width="2"/>
  </svg>

  <h1 class="title">DINNER OPTIONS</h1>
  <p class="subtitle">(an option below must be chosen for groups of 15 or more, served after 3pm)</p>
  <p class="note">*It is greatly appreciated if you are able to give pre-determined individual menu orders to help with food prep and operations of the event</p>

  <section class="option option-a">
    <h2 class="option-title">Option A - $20/Person</h2>
    <p class="option-desc">Served with bacon &amp; scallion mashed potatoes and steamed broccoli Also includes choice of starter house or Caesar salad</p>
    <ul class="dishes">
      <li>½ Copper Kettle’s Famous Wood-Roasted Chicken</li>
      <li>½ Slab Sweet &amp; Smoky BBQ Baby Back Ribs</li>
      <li>6 oz Fresh Norwegian Salmon</li>
      <li>6 oz Wood-Grilled Sirloin</li>
    </ul>
  </section>

  <section class="option option-b">
    <h2 class="option-title">Option B - $27/Person</h2>
    <p class="option-desc">Served with bacon &amp; scallion mashed potatoes and steamed broccoli Also includes choice of starter house or Caesar salad</p>
    <ul class="dishes">
      <li>30-Day Aged Wood-Grilled Ribeye – 14 oz</li>
      <li>6 oz Wood-Grilled Sirloin &amp; Grilled Shrimp</li>
      <li>½ Slab BBQ Ribs &amp; ¼ Wood-Roasted Chicken</li>
      <li>Full Rack of BBQ Baby Back Ribs</li>
    </ul>
  </section>

  <div class="gold-bar bar-top"></div>
  <div class="room-photo" role="img" aria-label="Photo of the private dining room with round tables set in white linen, a stone fireplace and tall windows"></div>
  <div class="gold-bar bar-bottom"></div>
</div>
</body>
</html>
```